Business Card For Halvenmoor Financial Consulting

Hi, I would like a business card designed. Bold, modern.
Please use the same design as the logo. I have also attached the website design to see the overall theme.
Wordmark Font
Color: Hex: #01AEF7

```html
<!DOCTYPE html>
<html lang="en">
<head>
<meta charset="utf-8">
<title>Halvenmoor Consulting — Business Card</title>
<link href="https://fonts.googleapis.com/css2?family=Montserrat:wght@400;500;700;800&display=swap" rel="stylesheet">
<style>
  :root {
    --bg: #7d7c7a;
    --paper: #fbfbfa;
    --navy: #0f2a4a;
    --ink-dark: #16222c;
    --accent: #01aef7;
    --accent-soft: #3aa0dc;
    --text: #3a3f45;
    --rule: #8fa3b6;
    --emboss: #0f1b24;
  }
  * { box-sizing: border-box; margin: 0; padding: 0; }
  html, body { width: 1200px; height: 801px; overflow: hidden; }
  body {
    background: var(--bg);
    font-family: "Montserrat", Arial, sans-serif;
    display: flex;
    align-items: center;
    justify-content: center;
    gap: 60px;
  }
  .card {
    width: 525px;
    height: 300px;
    position: relative;
    border-bottom: 4px solid var(--accent);
  }
  .card--front {
    background: var(--paper);
    display: flex;
    align-items: center;
    padding: 0 36px;
  }
  .brand {
    display: flex;
    align-items: center;
    gap: 12px;
  }
  .brand__mark {
    width: 30px;
    height: 30px;
    border: 3px solid var(--accent);
    flex: none;
  }
  .brand__name {
    font-weight: 800;
    font-size: 23px;
    letter-spacing: 0.5px;
    color: var(--navy);
    text-transform: uppercase;
    line-height: 1.05;
  }
  .card--front .brand { width: 226px; }
  .divider {
    width: 1.5px;
    height: 150px;
    background: var(--rule);
    margin: 0 22px 0 6px;
    flex: none;
  }
  .contact { color: var(--text); font-size: 12.5px; line-height: 1.45; }
  .contact__name {
    font-weight: 800;
    font-size: 18px;
    color: var(--navy);
    text-transform: uppercase;
    line-height: 1.1;
  }
  .contact__role { color: var(--accent-soft); font-size: 13px; margin-bottom: 14px; }
  .contact__address { margin-bottom: 14px; }
  .contact__row { display: flex; align-items: center; gap: 6px; }
  .contact__row svg { width: 11px; height: 11px; flex: none; fill: var(--accent-soft); }
  .card--back {
    background: var(--ink-dark);
    display: flex;
    align-items: center;
    justify-content: center;
  }
  .card--back .brand__mark { width: 48px; height: 48px; border-color: var(--emboss); }
  .card--back .brand__name { font-size: 34px; color: var(--emboss); }
</style>
</head>
<body>
  <section class="card card--front">
    <div class="brand">
      <span class="brand__mark"></span>
      <span class="brand__name">Halvenmoor<br>Consulting</span>
    </div>
    <div class="divider"></div>
    <div class="contact">
      <p class="contact__name">Marek Tolliver</p>
      <p class="contact__role">President</p>
      <p class="contact__address">18320 Seacliff Harbor<br>Seacliff CA 90210</p>
      <p class="contact__row">
        <svg viewBox="0 0 12 12"><path d="M2.5 1l2 2-1 1.5c.8 1.6 2 2.8 3.5 3.5L8.5 7l2 2-1.5 2C5 11 1 7 1 2.5z"/></svg>
        555-014-2287
      </p>
      <p class="contact__row">
        <svg viewBox="0 0 12 12"><path d="M1 2.5h10v7H1z M1 2.5l5 4 5-4" stroke="#fff" stroke-width=".8"/></svg>
        info@HalvenmoorConsulting.com
      </p>
      <p class="contact__row">
        <svg viewBox="0 0 12 12"><circle cx="6" cy="6" r="5"/></svg>
        www.HalvenmoorConsulting.com
      </p>
    </div>
  </section>

  <section class="card card--back">
    <div class="brand">
      <span class="brand__mark"></span>
      <span class="brand__name">Halvenmoor Consulting</span>
    </div>
  </section>
</body>
</html>
```